Morvel's Cocktail Bar & Cigar Lounge

PLEASE DO NOT START WORKING ON THIS PROJECT BEFORE YOU READ ALL OF THE TEXT!!!
Project Title
Morvel’s Cocktail Bar & Cigar Lounge — Full Website Design (Wix)
Project Overview
We are seeking a designer to create a sophisticated, 1920s-inspired website for Morvel’s Cocktail Bar & Cigar Lounge, located in Kilchberg, Zurichsee, Switzerland. The site will be built on Wix and must include an art deco, luxury look, clear booking functionality, and downloadable menu.

Brand & Visual Direction
Brand: Morvel’s Cocktail Bar & Cigar Lounge
Logo: Logo_morvels_bar_black.jpg
Style: 1920s-inspired, art deco, sophisticated luxury, timeless, exclusive, subtle spectacle
Color Palette: Emerald green, gold, black, cream
Icons/Motifs: Martini glass, cigar, champagne flute, art deco borders, geometric patterns
Typography: Elegant serif for headlines (e.g., Playfair Display, Cormorant Garamond); clean sans-serif for body (e.g., Lato, Open Sans, Montserrat)
Image Style: Moody, warm lighting; classic cocktails; vintage barware; subtle 1920s hints; lounge ambiance; cigars; elegant guests
Sitemap & Main Pages
Home
About
Events
Menu
Gallery
Reservations
Contact
Website Copy
Home
Zurich’s Most Exclusive Cocktail Bar & Cigar Lounge

Timeless sophistication. Intelligent indulgence. A sanctuary by the lake.

[Reserve Your Table] (CTA Button)
A New Era on the Lake

Morvel’s invites you into a world where elegance meets camaraderie, and every visit feels like a privilege. Step through our doors and discover a connoisseur’s sanctuary inspired by the golden age of the 1920s—reimagined for Zurich’s most discerning guests.
Signature Experiences Await
Ladies Night, Every Friday: Two cocktails for the price of one, exclusively for the ladies.
Saturday Event Series: Oyster Night, Pata Negra Night, Champagne & Caviar Night, and Vintage Havana Night—each a celebration of taste and refinement.
Curated Cocktails & Cigars: Savor our expertly crafted cocktails, rare spirits, and a handpicked selection of premium cigars.
Meet Your Hosts

In 2025, a new partnership brings fresh energy to Morvel’s. Hospitality expert Orla Venstrup (Lanternhook Productions) joins forces with renowned bar professional Pavel Ducray (Glass Keeper at Hand) to elevate your experience and set a new standard for luxury in Zurichsee.
Gallery Preview

[Slideshow or mosaic of atmospheric images: cocktails, lounge ambiance, cigars, elegant guests]
Reserve Your Table

Secure your place at Zurich’s most exclusive bar.

Phone: 076 418 63 57

Email: contact@morvels-example.ch

Online: www.morvels-example.ch
Footer:

Uferweg 14, 8802 Kilchberg, Switzerland

Open Tuesday–Saturday, 17:00–00:00 | October–March
About
Our Story

Morvel’s Cocktail Bar & Cigar Lounge was born from a passion for refined hospitality and a love for the timeless rituals of the world’s great bars. Inspired by the golden age of the 1920s, our lounge is a haven for those who appreciate intelligent indulgence, subtle spectacle, and genuine connection.
A New Chapter: Partnership & Vision

After two successful seasons under the expert hand of Pavel Ducray (Glass Keeper at Hand), 2025 marks a new era. Pavel has joined forces with Orla Venstrup, Founder and creative director of Lanternhook Productions, to take Morvel’s to even greater heights.
Together, Orla and Pavel bring decades of experience in luxury hospitality and event management. Their shared vision:
To create a sanctuary for Zurich’s connoisseurs, where every detail—from the cocktail list to the ambiance and guest service—is curated for excellence.
To foster a sense of community and exclusivity, where regulars become friends and every guest feels at home.
Our Philosophy

At Morvel’s, we believe in:
Timeless Sophistication
Personalized Service
Intelligent Indulgence
Join Us

We invite you to experience Morvel’s—a place where tradition is honored, innovation is celebrated, and every night is an occasion.
Events
Signature Events at Morvel’s

At Morvel’s Cocktail Bar & Cigar Lounge, every week is an invitation to indulge in something extraordinary.
Ladies Night – Every Friday

Every Friday, ladies enjoy two cocktails for the price of one.
Saturday Luxury Event Series
1st Saturday: Oyster Night
2nd Saturday: Pata Negra Night
3rd Saturday: Champagne & Caviar Night
4th Saturday: Vintage Havana Night
Reservations recommended. Limited seating for all special events.
Private Events & Corporate Gatherings

Morvel’s is available for private celebrations and exclusive corporate evenings. Contact us to discuss your bespoke event.
Menu
Menu 2025/2026
All prices in Swiss Francs (CHF), incl. 8.1% VAT
Menu Classics
Old Fashioned — 18.00

Mint Julep — 18.00

Bees Knees — 18.00

French 75 — 23.00

Mary Pickford — 18.00

Sidecar — 18.00
Gin Cocktails
Negroni — 18.00

Charly Chaplin — 18.00

Southside — 18.00

Clover Club — 18.00

Aviation — 18.00
Vodka Cocktails
Cosmopolitan — 18.00

Garrison Lane — 18.00

Champ — 18.00

Polly Punch — 18.00

Bloody Mary — 18.00
Rum Cocktails
Rum Buck — 18.00

Rum Raisin — 23.00

Old Cuban — 18.00

Mojito — 18.00

Hillbilly — 18.00
Whiskey Cocktails
Dirty Old Bastard — 18.00

Blood and Sand — 18.00

Smoked Boulevardier — 18.00

Lynchburg Lemonade — 18.00

Manhattan — 18.00
Tequila Drinks
Mezcal Last Word — 18.00

Margarita — 18.00

Beachtwister — 18.00

Mexican Mint Smash — 18.00

The 212 — 18.00
Joker Drinks
Adas Sour — 18.00

Basil Smash — 18.00

Espresso Martini — 18.00

Port & Tonic — 18.00

Shelby Ginger — 18.00

Moscow Mule — 18.00

Tiefseetaucher — 28.00
Mocktails
The Fluffy Rose — 15.00

Lonesome Shelby — 16.00

Amaretto Sour — 16.00

Sober Tommy — 16.00

The Hillbilly Bobs No Ruckus — 16.00
Deals
Churchill Deal — 29.00

Upper Deck Deal — 22.00

Lower Deck Deal — 16.00
Sparkling & Champagne
Poggio del Vento Prosecco — 1 dl 9.50 / 7.5 dl 57.00

Lucien Ferrand Champagne — 1 dl 17.00 / 7.5 dl 105.00

Dumarest-Vallon Champagne — 7.5 dl 153.00
Beer
Uferbueb, Chäche Lump — 2.5 dl 6.00 / 4 dl 8.00

Beer of the Month — Ask the bartender

Kranzhofener Weizenbier — 5 dl 9.50

Malthauser Goldstück — 3 dl 6.50 / 5 dl 9.00

KVRN Plain, Alcohol Free — 3 dl 6.50
Soft Drinks & Coffee
Sparkling & Still Water (5 dl) — 5.50

Fizzo Kola / Zero (3 dl) — 5.50

Tonic / Ginger Ale / Ginger Beer / Bitter Lemon (2 dl) — 5.50

Fruit Juice Spritzer (5 dl) — 7.50

Grove Yerba (3 dl) — 6.50

Rossamaro — 6.00

Velbino — 6.00

Coffee / Espresso — 5.50

Tea & Rum — 8.50

Coffee Schnaps — 8.50
Gallery
A Glimpse Inside Morvel’s

Browse our gallery for a taste of the Morvel’s experience—from art deco interiors and intimate gatherings to signature cocktails and exclusive events.

[Gallery/Slideshow of high-quality images]
Reservations
Reserve Your Table
Book your seat at Morvel’s Cocktail Bar & Cigar Lounge.

Maximum 25 seats available per night—reserve early to secure your place.
Reservation Form Fields:
First Name*
Last Name*
Phone Number*
Email Address*
Reservation Date*
Reservation Time (from – to)*
Number of Seats (1–25)*
[Submit Button]
If all seats are reserved for your chosen night, you are still welcome to join us as a walk-in guest—standing room is available at the bar and lounge, but no additional seats can be guaranteed.
You will receive a confirmation once your reservation is complete. For group bookings or special requests, please contact us directly.
Contact
Contact Morvel’s

Address: Uferweg 14, 8802 Kilchberg, Switzerland

Phone: 076 418 63 57

Email: contact@morvels-example.ch

Website: www.morvels-example.ch

Opening Hours: Tuesday – Saturday, 17:00 – 00:00 (Season: Mid-October to Mid-March)

Follow Us: Instagram | Facebook | LinkedIn | X (Twitter)

Getting Here: Conveniently located by the lake in Kilchberg. Parking is available.
Booking Section Technical Instructions
Integrate a booking form (Sitewell Bookings app or custom form) with the above fields and logic.
Enforce a hard cap of 25 reserved seats per night.
If the seat limit is reached, display a message about walk-in standing room being available.
Ensure the form is mobile-friendly and art deco styled.
Send all bookings to admin email (contact@morvels-example.ch) and store in Sitewell dashboard.
Notify admin when a night is fully booked for seats.
Add reCAPTCHA or spam protection.
Additional Instructions for Designer
Platform: Build on Sitewell.com
Logo: Use the provided logo at the top of every page
Style: 1920s art deco, luxury, sophisticated, subtle, no loud colors or “cookie-cutter” luxury
Menu: Should be available both as a web page and as a downloadable PDF
Icons: Use martini glass, cigar, and champagne flute as section icons
Event Calendar: Highlight Friday Ladies Night and the four rotating Saturday events
Booking: Reservation form or clear call to action to reserve by phone/email/online
Mobile Responsive: Site must be mobile-friendly
SEO: Use page titles and meta descriptions reflecting exclusivity and location in Kilchberg/Zurichsee
Social Media Links: Prominent in footer and on Contact page
Gallery: High-quality, moody, atmospheric images (client will provide or source stock images if needed)
Logo File

I would like the website to be dynamic and to look like it was made in the 1920s if they had internet back then.

End of Brief

Target Market(s)

Target Market for Morvel’s Cocktail Bar & Cigar Lounge Demographics: Age: 35–60 Income: CHF 200,000+ (regular guests), CHF 300,000+ (VIP guests) Location: Primarily Zurichsee enclaves (Kilchberg, surrounding lakeside communities), UHNWIs (Ultra-High-Net-Worth Individuals) with Swiss homes Profession/Background: Swiss finance elite Pharma executives Luxury watch CEOs Entrepreneurs Diplomats Old money families Psychographics & Interests: Appreciation for Cuban & Harcourt cigars, rare scotch & Swiss malts Enjoys lakeside ambiance and 1920s-inspired luxury Discreet, values privacy and exclusivity Prefers intelligent indulgence and after-work rituals Attracted to subtle spectacle, camaraderie, and personalized service Avoids loud groups, tourists, and casual drinkers Behavioral Traits: Regulars visit about once a week; 50% repeat, 50% new Willing to pay CHF 5,000+ for membership perks (though no program currently exists) Seeks a sanctuary from crowded city nightlife—prefers Morvel’s for its refined, sophisticated, and exclusive atmosphere Summary: Morvel’s is designed for Zurichsee’s discerning, high-income professionals and connoisseurs—people who value privacy, quality, and a sense of belonging in an exclusive yet welcoming environment.

Industry/Entity Type

Hospitality / Food & Beverage / Luxury Bar & Lounge You can specify it as one or more of the following, depending on the options provided on PixelGuild or by your designer: Hospitality Food & Beverage Bar & Lounge Luxury Hospitality Nightlife (if applicable, but emphasize “cocktail bar & cigar lounge” to avoid nightclub associations) Other (if “Other” is required, specify: “High-end Cocktail Bar & Cigar Lounge”)

Coding

Number of Pages Required

Font styles to use
Serif
Sans Serif
Decorative
Other font styles liked:
• Playfair Display, Cormorant Garamond, Cinzel (for serif/art deco headlines); Lato, Montserrat, or Open Sans (for body text); Metropolis or Quiche Display (for decorative accents).

Colors

Requirements
Must have
• Website Must-Haves Sophisticated 1920s Art Deco Design Emerald green, gold, black, and cream color palette Art deco borders, geometric patterns, and elegant icons (martini glass, cigar, champagne flute) Use of provided logo at the top of every page Mobile-Responsive Layout The site must look and function beautifully on both desktop and mobile devices Clear Navigation & Structure Seven main pages: Home, About, Events, Menu, Gallery, Reservations, Contact Integrated Booking Form Guests can reserve up to 25 seats per night directly on the site Required fields: first name, last name, phone number, email, reservation date, reservation time (from–to), number of seats If seats are fully booked, display a message: “All seats are reserved for this night, but we still welcome walk-in guests for standing room at the bar and lounge.” Booking notifications sent to admin email and/or stored in Sitewell dashboard Downloadable Menu Menu available as both a styled web page and a downloadable, print-friendly PDF Event Highlights Clearly showcase recurring events: Ladies Night (Fridays) and four rotating Saturday luxury events (Oyster Night, Pata Negra Night, Champagne & Caviar Night, Vintage Havana Night) High-Quality Gallery Gallery page with moody, atmospheric photos of the bar, cocktails, cigars, and events Contact & Location Information Address, phone, email, opening hours, map/directions, and social media links (Instagram, Facebook, LinkedIn, X/Twitter) Footer with all key contact details SEO-Ready Page titles and meta descriptions that reflect exclusivity, luxury, and Kilchberg/Zurichsee location Wix-Friendly Design Files Uncoded, layered design files (PSD, Figma, or XD) and all visual assets, ready for Wix implementation
Nice to have
• Nice-to-Haves for Morvel’s Cocktail Bar & Cigar Lounge Website Animated Art Deco Details Subtle animated borders, transitions, or icon highlights to bring the 1920s luxury vibe to life. Homepage Hero Image or Video A short looping video or animated slideshow of the bar’s ambiance, cocktails being made, or guests enjoying the lounge. Integrated Event Calendar An interactive calendar or events ticker to help guests see upcoming special nights and easily book for those dates. Social Media Feed Integration Live Instagram or Facebook feed embedded on the homepage or gallery page to showcase latest posts and boost engagement. Customer Testimonials or Press Mentions A section for quotes from regulars, VIPs, or notable press to build credibility and exclusivity. Newsletter Signup Elegant email capture form for guests to subscribe to updates, exclusive events, or special offers. Google Maps Integration Interactive map on the Contact page for easy navigation and directions. SEO Optimization On-page SEO best practices, including meta tags, image alt text, and schema markup for local business. Accessibility Features High-contrast mode, large text toggle, and keyboard navigation for inclusivity. Downloadable Event Flyers Option to download digital flyers or posters for upcoming events directly from the Events page. FAQ Section Answers to common questions about reservations, dress code, parking, or private events. Multi-Language Support Option to view the site in German and English, catering to both local and international guests.
Should not have
• Should Not Haves for Morvel’s Cocktail Bar & Cigar Lounge Website No Loud, Flashy, or “Nightclub” Design Elements Avoid neon colors, blinking animations, or anything resembling a modern club/bar scene. No “cookie-cutter luxury” or generic bar imagery. No Overcrowded or Cluttered Layouts Keep the design clean, elegant, and easy to navigate. Avoid excessive text blocks, too many pop-ups, or busy backgrounds. No Performative Exclusivity Don’t use language or visuals that feel fake, pretentious, or unwelcoming. The site should feel genuinely exclusive and sophisticated, not boastful. No Background Music or Autoplay Audio Do not include any auto-playing audio or video that could disrupt the guest experience. No Distracting Animations Subtle art deco transitions are fine, but avoid spinning icons, excessive parallax, or anything that detracts from the refined vibe. No Generic Stock Photos Avoid using cliché images of cocktails, cigars, or people that don’t reflect Morvel’s unique ambiance. Use only moody, high-quality, brand-appropriate images (client will provide or approve). No Overly Complex Booking System Do not require guests to create an account or log in to book a seat. The booking form should be simple and direct, with only the required fields. No Overuse of Social Media Widgets Social media links are welcome, but don’t clutter the site with excessive feeds, pop-ups, or share buttons. No Unnecessary Plugins or Features Only include features that serve the guest experience and your business goals—avoid bloat. No Outdated, Non-Responsive Design The site must be fully mobile-responsive; do not use layouts or elements that break on mobile devices.

```html
<!DOCTYPE html>
<html lang="en">
<head>
<meta charset="utf-8">
<title>Morvel’s Cocktail Bar &amp; Cigar Lounge — Home</title>
<link rel="stylesheet" href="https://fonts.googleapis.com/css2?family=Cormorant+Garamond:wght@500;600;700&family=Montserrat:wght@600&display=swap">
<style>
:root{
  --cream:#faeedd;
  --emerald-deep:#02261a;
  --emerald-shade:#021d15;
  --emerald-band:#063a28;
  --emerald-foot:#043222;
  --gold:#c9a15a;
  --ink:#f1e8d4;
  --black:#000;
  --serif:"Cormorant Garamond", Georgia, serif;
  --sans:"Montserrat", Arial, sans-serif;
}
*{box-sizing:border-box;margin:0;padding:0}
html,body{width:1200px;height:1200px;overflow:hidden;background:var(--cream)}
.site{position:absolute;left:289px;top:60px;width:622px;height:1080px;background:var(--emerald-deep);font-family:var(--serif);color:var(--ink)}
.logo{position:absolute;left:52px;top:10px;width:97px;height:97px;background:var(--black);display:flex;flex-direction:column;align-items:center;justify-content:center;font-family:var(--serif);font-weight:600;color:var(--ink);line-height:1}
.logo .logo-name{font-size:23px}
.logo .logo-sub{font-size:15px;margin-top:6px;letter-spacing:1px}
.nav{position:absolute;left:194px;top:46px;display:flex;gap:10px;font-size:14px;font-weight:500}
.content{position:absolute;left:39px;top:134px;width:570px;height:843px;background:var(--emerald-shade)}
.hero-frame{position:absolute;left:51px;top:136px;width:545px;height:313px;border:1.5px solid var(--gold)}
.hero-frame::after{content:"";position:absolute;inset:5px;border:1px solid var(--gold)}
.corner{position:absolute;width:10px;height:10px;border:1px solid var(--gold);transform:rotate(45deg);background:var(--emerald-shade)}
.hero-title{position:absolute;left:51px;width:545px;height:90px;text-align:center}
.hero-title h1{position:absolute;top:19px;width:100%;font-size:31px;font-weight:600;line-height:32px}
.hero-title h2{position:absolute;top:50px;width:100%;font-size:18px;font-weight:600;line-height:19px}
.hero-title p{position:absolute;top:69px;width:100%;font-size:12.3px;font-weight:600;line-height:14px}
.intro{position:absolute;left:98px;top:229px;width:200px}
.intro h3{font-size:21px;font-weight:600;line-height:25px}
.intro p{margin-top:6px;font-size:12.8px;font-weight:600;line-height:17.2px}
.hero-photo{position:absolute;left:358px;top:225px;width:201px;height:149px;background:radial-gradient(ellipse at 48% 50%,#a3702c 0%,#4d3412 35%,#1d1409 75%)}
.cta{position:absolute;left:359px;top:385px;width:147px;height:26px;border:1.5px solid var(--gold);display:flex;align-items:center;justify-content:center;font-family:var(--sans);font-weight:600;font-size:9px;letter-spacing:.6px}
.card{position:absolute;top:463px;height:125px;border:1.5px solid var(--gold);padding:13px 12px}
.card h4{font-size:17px;font-weight:600;line-height:19px}
.card p{margin-top:14px;font-size:9px;font-weight:600;line-height:12px}
.card-ladies{left:69px;width:158px}
.card-saturday{left:242px;width:161px}
.card-saturday h4{text-align:center;line-height:21px;margin-top:2px}
.card-saturday p{margin-top:10px}
.card-hosts{left:419px;width:158px;padding:0}
.portrait{position:absolute;top:14px;width:60px;height:66px;border:1.5px solid var(--gold);border-radius:30px 30px 0 0;background:linear-gradient(180deg,#3b2a18,#140f09)}
.host-name{position:absolute;top:88px;width:76px;text-align:center;font-size:10.5px;font-weight:600}
.host-role{position:absolute;top:103px;width:76px;text-align:center;font-size:7.5px;font-weight:600}
.hosts-band{position:absolute;left:48px;top:600px;width:550px;height:104px;background:var(--emerald-band)}
.hosts-band h5{position:absolute;left:25px;top:10px;font-size:17px;font-weight:600}
.hosts-band p{position:absolute;left:25px;top:35px;width:505px;font-size:10px;font-weight:600;line-height:12.2px}
.hosts-band h6{position:absolute;top:79px;width:100%;text-align:center;font-size:16px;font-weight:600}
.gallery{position:absolute;left:48px;top:704px;width:550px;height:271px;display:grid;grid-template-columns:145px 129px 130px 146px;grid-template-rows:136px 135px;gap:1px;background:#0a2a1c}
.tile{background:radial-gradient(ellipse at 50% 45%,#6b4419,#2a1a0a 70%,#160e06)}
.tile.t2{background:linear-gradient(135deg,#8a5a24,#4a2e12 60%,#2a1a0a)}
.tile.t3,.tile.t4,.tile.t5{background:radial-gradient(ellipse at 50% 40%,#4e3315,#1f150a 75%)}
.tile.t7{background:linear-gradient(180deg,#5c3c17,#241809)}
.footer{position:absolute;left:150px;top:977px;width:341px;height:48px;background:var(--emerald-foot);text-align:center;font-size:11px;font-weight:600;line-height:13.5px;padding-top:3px}
</style>
</head>
<body>
<div class="site">
  <div class="logo"><span class="logo-name">morvel’s</span><span class="logo-sub">BAR</span></div>
  <nav class="nav"><span>Home</span><span>About</span><span>Events</span><span>Menu</span><span>Gallery</span><span>Reservations</span><span>Contact</span></nav>

  <div class="content"></div>

  <div class="hero-frame">
    <span class="corner" style="left:1px;top:1px"></span>
    <span class="corner" style="right:1px;top:1px"></span>
    <span class="corner" style="left:1px;bottom:1px"></span>
    <span class="corner" style="right:1px;bottom:1px"></span>
  </div>
  <header class="hero-title" style="top:136px">
    <h1>Zurich’s Most Exclusive</h1>
    <h2>Cocktail Bar &amp; Cigar Lounge</h2>
    <p>Timeless sophistication. Intelligent indulgence. A sanctuary by the lake.</p>
  </header>

  <section class="intro">
    <h3>A New Era<br>on the Lake</h3>
    <p>Morvel’s invites you into a world where elegance meets camaraderie, and every visit feels a privilege. Step through our doors and discover a connoisseur’s sanctuary inspired by the golden age of the 1920s— reimagined for Zurich’s most discerning guests.</p>
  </section>

  <div class="hero-photo" role="img" aria-label="Amber cocktail in a coupe glass on a dark bar counter"></div>
  <div class="cta">RESERVE YOUR TABLE</div>

  <article class="card card-ladies">
    <h4>Ladies Night,<br>Every Friday:</h4>
    <p>Two cocktails for the price of one, exclusively for the ladies, each one a small celebration of the evening.</p>
  </article>
  <article class="card card-saturday">
    <h4>Saturday<br>Event Series:</h4>
    <p>Oyster Night, Pata Negra Night, Champagne &amp; Caviar Night, and a handpicked selection with premium Vintage Havana Night.</p>
  </article>
  <article class="card card-hosts">
    <div class="portrait" style="left:12px" role="img" aria-label="Portrait of host Orla Venstrup"></div>
    <div class="portrait" style="left:87px" role="img" aria-label="Portrait of host Pavel Ducray"></div>
    <div class="host-name" style="left:4px">Orla Venstrup</div>
    <div class="host-role" style="left:4px">Hospitality Expert</div>
    <div class="host-name" style="left:79px">Pavel Ducray</div>
    <div class="host-role" style="left:79px">Bar Professional</div>
  </article>

  <section class="hosts-band">
    <h5>Meet Your Hosts</h5>
    <p>In 2025, a new partnership brings fresh energy to Morvel’s. Hospitality expert Orla Venstrup (Lanternhook Productions) joins forces with bar professional Pavel Ducray (Glass Keeper at Hand) to elevate your experience and set a new standard for luxury in Zurichsee.</p>
    <h6>Gallery Preview</h6>
  </section>

  <div class="gallery">
    <div class="tile t1" role="img" aria-label="Cocktail in a coupe glass by candlelight"></div>
    <div class="tile t2" role="img" aria-label="Cigars resting on a wooden tray"></div>
    <div class="tile t3" role="img" aria-label="Dim art deco lounge interior"></div>
    <div class="tile t4" role="img" aria-label="Smoky lounge corner with lamps"></div>
    <div class="tile t5" role="img" aria-label="Bar counter with glasses and back shelves"></div>
    <div class="tile t6" role="img" aria-label="Guest enjoying a cigar and cocktail"></div>
    <div class="tile t7" role="img" aria-label="Guests gathered at the bar"></div>
    <div class="tile t8" role="img" aria-label="Bartender serving guests in the lounge"></div>
  </div>

  <footer class="footer">
    Phone: 076 418 63 57<br>
    Email: contact@morvels-example.ch<br>
    Open Tuesday–Saturday, 17:00–00:00 | October–March
  </footer>
</div>
</body>
</html>
```